Business Card Design Project

I would like to have a project of business card with incorporated attachted logo elements in warm colors like: gold, yellow, brown.
We would like incorporate below information into the design
Name of the Company: Continental Ribbon Masters
Name: Darrell Finch
Position: Project Director
e-mail: darrell@ribbonmasters-demo.com
mobile: +65 83417729
website: www.ribbonmasters-demo.com
Address: 47 Marlow Road, #05-11, Singapore 417256
There is a picture attachted which can be used as a back side of the buisness card - we would like to follow the colors theme on the front card ( with the person contact details) how ever the front card we will prefer with white background but with graphfic elements coming from logo.
Reason: the project has been launched on 24 of April with deadline by 24 of April by mistakes. Thats why I would like to extend the deadline.
Name: Darrell Finch
mobile: +65 83417729

```html
<!DOCTYPE html>
<html lang="en">
<head>
<meta charset="utf-8">
<title>Continental Ribbon Masters – Business Card</title>
<link rel="stylesheet" href="https://fonts.googleapis.com/css2?family=Montserrat:wght@400;600;700&family=Open+Sans:wght@400;600&display=swap">
<style>
  :root {
    --page-bg: #d9d9d9;
    --gold-deep: #b8841c;
    --gold-mid: #d0a41a;
    --gold-bright: #e4cc10;
    --brown: #7a5a12;
    --ink: #0a0a0b;
    --white: #ffffff;
    --rule: #8a8a8a;
  }
  * { margin: 0; padding: 0; box-sizing: border-box; }
  html, body {
    width: 1200px; height: 900px; overflow: hidden;
    background: var(--page-bg);
  }
  .card {
    position: absolute;
    width: 614px; height: 338px;
    border-radius: 16px;
    overflow: hidden;
    box-shadow: 0 4px 10px rgba(0,0,0,.35);
  }
  .card svg.art { position: absolute; inset: 0; }

  /* Front */
  .card-front {
    left: 104px; top: 72px;
    background: radial-gradient(ellipse 260px 200px at 250px 40px, #e6d20e 0%, var(--gold-mid) 55%, var(--gold-deep) 100%);
  }
  .emblem-photo {
    position: absolute; left: 100px; top: 34px;
    width: 190px; height: 266px;
    border-radius: 48% 48% 30% 30%;
    background: radial-gradient(ellipse at 55% 40%, #8a6a2a 0%, #7a5c22 45%, rgba(122,92,34,0) 75%);
  }
  .brand-name {
    position: absolute; left: 104px; top: 20px;
    font-family: "Montserrat", sans-serif; font-weight: 600;
    font-size: 12px; letter-spacing: .5px; color: var(--white);
  }
  .holder-name {
    position: absolute; left: 229px; top: 226px;
    font-family: "Montserrat", sans-serif; font-size: 31px;
    color: var(--white); letter-spacing: -.3px; white-space: nowrap;
  }
  .holder-name .first { font-weight: 700; }
  .holder-name .last { font-weight: 400; }
  .name-rule {
    position: absolute; left: 229px; right: 0; top: 262px;
    height: 1px; background: rgba(255,255,255,.55);
  }
  .holder-title {
    position: absolute; left: 231px; top: 265px;
    font-family: "Open Sans", sans-serif; font-size: 12.5px; color: var(--white);
  }

  /* Back */
  .card-back {
    left: 484px; top: 482px;
    background: var(--ink);
  }
  .contact-divider {
    position: absolute; left: 52px; top: 88px;
    width: 1px; height: 196px; background: var(--rule);
  }
  .contact-list { position: absolute; left: 0; top: 186px; list-style: none; }
  .contact-item {
    position: relative; height: 19px;
    display: flex; align-items: center;
    font-family: "Open Sans", sans-serif; font-size: 11.5px; color: var(--white);
    border-bottom: 1px solid var(--rule);
    padding-left: 58px;
  }
  .contact-item .icon {
    position: absolute; left: 32px; top: 4px;
    width: 13px; height: 13px;
  }
  .contact-item.phone   { width: 248px; font-size: 13px; }
  .contact-item.email   { width: 301px; }
  .contact-item.web     { width: 349px; }
  .contact-item.address { width: 404px; }
</style>
</head>
<body>

<section class="card card-front" aria-label="Business card front">
  <svg class="art" viewBox="0 0 614 338" aria-hidden="true">
    <defs>
      <linearGradient id="front-band" x1="0" y1="0" x2="1" y2="0">
        <stop offset="0" stop-color="#b98a1a"/>
        <stop offset=".6" stop-color="#d7b414"/>
        <stop offset="1" stop-color="#e6d00c"/>
      </linearGradient>
    </defs>
    <path d="M0 170 C60 250 150 300 250 300 C380 300 480 270 614 338 L0 338 Z" fill="var(--brown)"/>
    <path d="M0 182 C60 258 150 306 250 306 C380 306 480 282 614 338 L0 338 Z" fill="url(#front-band)"/>
    <path d="M0 240 C100 290 220 312 330 300 C440 290 520 300 614 338 L0 338 Z" fill="#c79a18" opacity=".7"/>
  </svg>
  <div class="emblem-photo" role="img" aria-label="Photograph of a performer on a vertical pole"></div>
  <p class="brand-name">Continental Ribbon Masters</p>
  <h1 class="holder-name"><span class="first">Darrell</span><span class="last">Finch</span></h1>
  <div class="name-rule"></div>
  <p class="holder-title">Project Director</p>
</section>

<section class="card card-back" aria-label="Business card back">
  <svg class="art" viewBox="0 0 614 338" aria-hidden="true">
    <defs>
      <linearGradient id="back-band" x1="0" y1="0" x2="1" y2="0">
        <stop offset="0" stop-color="#e4cf0e"/>
        <stop offset=".5" stop-color="#c9a51a"/>
        <stop offset="1" stop-color="#b8861c"/>
      </linearGradient>
    </defs>
    <path d="M0 338 C80 300 200 292 330 300 C470 308 560 260 614 150 L614 338 Z" fill="var(--brown)"/>
    <path d="M0 338 C90 304 210 298 335 306 C480 316 570 270 614 178 L614 338 Z" fill="var(--gold-bright)"/>
    <path d="M0 338 C100 310 220 306 340 314 C490 322 575 280 614 200 L614 338 Z" fill="url(#back-band)"/>
  </svg>
  <div class="contact-divider"></div>
  <ul class="contact-list">
    <li class="contact-item phone">
      <svg class="icon" viewBox="0 0 14 14"><circle cx="7" cy="7" r="7" fill="#fff"/><path d="M4.3 3.6l1.3-.3.8 1.8-.9.7c.5 1 1.2 1.7 2.2 2.2l.7-.9 1.8.8-.3 1.3c-3 .2-5.8-2.6-5.6-5.6z" fill="#0a0a0b"/></svg>
      +65 83417729
    </li>
    <li class="contact-item email">
      <svg class="icon" viewBox="0 0 14 14"><circle cx="7" cy="7" r="7" fill="#fff"/><rect x="3.5" y="4.5" width="7" height="5" rx=".6" fill="#0a0a0b"/><path d="M3.8 4.9L7 7.3l3.2-2.4" stroke="#fff" stroke-width=".7" fill="none"/></svg>
      darrell@ribbonmasters-demo.com
    </li>
    <li class="contact-item web">
      <svg class="icon" viewBox="0 0 14 14"><circle cx="7" cy="7" r="7" fill="#fff"/><circle cx="7" cy="7" r="3.6" fill="none" stroke="#0a0a0b" stroke-width=".8"/><path d="M3.4 7h7.2M7 3.4c-1.6 2-1.6 5.2 0 7.2M7 3.4c1.6 2 1.6 5.2 0 7.2" stroke="#0a0a0b" stroke-width=".7" fill="none"/></svg>
      www.ribbonmasters-demo.com
    </li>
    <li class="contact-item address">
      <svg class="icon" viewBox="0 0 14 14"><circle cx="7" cy="7" r="7" fill="#fff"/><path d="M7 3a2.6 2.6 0 0 0-2.6 2.6C4.4 7.6 7 11 7 11s2.6-3.4 2.6-5.4A2.6 2.6 0 0 0 7 3z" fill="#0a0a0b"/><circle cx="7" cy="5.6" r="1" fill="#fff"/></svg>
      47 Marlow Road, #05-11, Singapore 417256
    </li>
  </ul>
</section>

</body>
</html>
```